Moravel Aesthetic Doctor

I require an elegant, luxurious looking business card for my aesthetic business. I am a doctor and that will set me aside from competitors. I am planning to provide home and spa based treatments to clients with high expectations. I have attached my logo.

```html
<!DOCTYPE html>
<html lang="en">
<head>
<meta charset="utf-8">
<title>Moravel Aesthetic Doctor – Business Card</title>
<link rel="stylesheet" href="https://fonts.googleapis.com/css2?family=Montserrat:wght@400;500&display=swap">
<style>
  :root {
    --backdrop: #2e2e2f;
    --card: #ffffff;
    --blue: #3a90d0;
    --blue-soft: #8fc8ee;
    --grey: #9a9a9c;
    --grey-line: #a7a7a9;
    --ink: #3c3c3e;
  }
  * { margin: 0; padding: 0; box-sizing: border-box; }
  html, body {
    width: 1200px; height: 1192px; overflow: hidden;
    background: var(--backdrop);
    font-family: "Montserrat", sans-serif;
  }
  .card {
    position: absolute;
    left: 189px; width: 827px; height: 472px;
    background: var(--card);
    border-radius: 26px;
    overflow: hidden;
  }
  .card--front { top: 111px; }
  .card--back { top: 616px; height: 468px; }

  .brand { position: absolute; display: flex; align-items: center; color: var(--grey); font-weight: 400; }
  .brand__mark { border-radius: 50%; background: var(--blue-soft); flex: none; }
  .brand__name { line-height: 1; letter-spacing: 0.04em; text-transform: uppercase; }
  .brand__name span { display: block; }

  .card--front .brand { left: 78px; top: 190px; gap: 16px; }
  .card--front .brand__mark { width: 56px; height: 56px; }
  .card--front .brand__name span:first-child { font-size: 42px; }
  .card--front .brand__name span:last-child { font-size: 16px; margin-top: 6px; letter-spacing: 0.06em; }

  .divider {
    position: absolute; left: 426px; top: 152px;
    width: 2px; height: 166px; background: var(--blue);
  }
  .details { position: absolute; left: 452px; top: 146px; color: var(--ink); }
  .details__name { font-size: 23px; font-weight: 500; color: var(--blue); }
  .details__name small { font-size: 12px; color: var(--ink); font-weight: 400; margin-left: 4px; }
  .details__cred { font-size: 18px; line-height: 24px; margin-top: 6px; }
  .contacts { list-style: none; margin-top: 22px; }
  .contacts li { display: flex; align-items: center; gap: 12px; font-size: 18px; line-height: 26px; }
  .contacts svg { width: 14px; height: 14px; fill: var(--blue); flex: none; }

  .band { position: absolute; left: 0; top: 412px; width: 827px; height: 60px; }
  .follow {
    position: absolute; left: 544px; top: 432px;
    display: flex; align-items: center; gap: 14px;
    color: #fff; font-size: 25px;
  }
  .follow__dot { width: 20px; height: 20px; border-radius: 50%; background: #fff; }
  .follow__dot:first-of-type { margin-left: 16px; }

  .card--back .brand { left: 50%; transform: translateX(-50%); top: 104px; gap: 22px; }
  .card--back .brand__mark { width: 84px; height: 84px; }
  .card--back .brand__name span:first-child { font-size: 62px; }
  .card--back .brand__name span:last-child { font-size: 23px; margin-top: 8px; letter-spacing: 0.06em; }

  .services {
    position: absolute; left: 0; right: 0; top: 332px;
    text-align: center; color: var(--ink); font-size: 20px; line-height: 26px;
  }
  .services__tagline { color: var(--blue); font-size: 26px; line-height: 34px; margin-top: 2px; }
</style>
</head>
<body>
  <section class="card card--front">
    <div class="brand">
      <div class="brand__mark"></div>
      <div class="brand__name"><span>Moravel</span><span>Aesthetic Doctor</span></div>
    </div>
    <div class="divider"></div>
    <div class="details">
      <p class="details__name">Dr Elena Varga<small>MRCPCH MD</small></p>
      <p class="details__cred">Australasian Diploma<br>&nbsp;of Aesthetic Medicine</p>
      <ul class="contacts">
        <li><svg viewBox="0 0 16 16"><path d="M3.5 1l2.5 3-1.5 2c1 2 3 4 5 5l2-1.5 3 2.5-1.5 2.5C7 15 1 9 1 3z"/></svg>0800 555 014</li>
        <li><svg viewBox="0 0 16 16"><path d="M1 4h14v1l-7 4.5L1 5z M1 7l7 4.5L15 7v6H1z"/></svg>elena@moravel.co.nz</li>
        <li><svg viewBox="0 0 16 16"><path d="M8 1a7 7 0 100 14A7 7 0 008 1zm0 1.5c.9 0 1.8 2 2 4.5H6c.2-2.5 1.1-4.5 2-4.5zM2.6 7h2c0-1.6.4-3 .9-4A5.5 5.5 0 002.6 7zm8.8 0h2a5.5 5.5 0 00-2.9-4c.5 1 .9 2.4.9 4zM2.6 9a5.5 5.5 0 002.9 4c-.5-1-.9-2.4-.9-4zm3.4 0c.2 2.5 1.1 4.5 2 4.5s1.8-2 2-4.5zm5.4 0c0 1.6-.4 3-.9 4a5.5 5.5 0 002.9-4z"/></svg>www.moravel.co.nz</li>
      </ul>
    </div>
    <svg class="band" viewBox="0 0 827 60" preserveAspectRatio="none" aria-hidden="true">
      <path d="M0 26 H440 C458 26 468 8 492 6 H827 V11 H496 C476 13 464 34 442 34 H0 Z" fill="var(--grey-line)"/>
      <path d="M0 38 H450 C470 38 480 20 505 18 H827 V60 H0 Z" fill="var(--blue)"/>
    </svg>
    <div class="follow">Follow<span class="follow__dot"></span><span class="follow__dot"></span></div>
  </section>

  <section class="card card--back">
    <div class="brand">
      <div class="brand__mark"></div>
      <div class="brand__name"><span>Moravel</span><span>Aesthetic Doctor</span></div>
    </div>
    <div class="services">
      <p>Dermal injectables - Plasma facials - Microneedling</p>
      <p>Skin boosters - Excessive sweating</p>
      <p class="services__tagline">Home and Spa Based Treatments</p>
    </div>
  </section>
</body>
</html>
```